TK Homes - Stone Dorf Design

Looking for a double sides design, 1 side for my realestate and the other for home building. ( TK Homes on 1 side, Stone Dorf card on the other Side
Side 1 - Marek Tove ~ Vox Realty logo and Company ( the Property quarter )
Marek Tove
Marek@Marektove.example
IG - Marek_Bzq_Realtor
FB - marekt
Cell - 5558130467
3847 61 St Nw

Side 2
Marek Tove
5558130467
IG - Stonedorf_Bzq
Stonedorfdev@mailbox.example

Target Market(s)

Home buyers/ sellers

Industry/Entity Type

Home builders - Realestate

Contact Information for Business Card

Above

Requirements
Must have
• Black OR White background - my information -

```html
<!DOCTYPE html>
<html lang="en">
<head>
<meta charset="utf-8">
<title>TK Homes / Stone Dorf business cards</title>
<link rel="stylesheet" href="https://fonts.googleapis.com/css2?family=Cinzel:wght@400;600&family=Tinos&display=swap">
<style>
  :root {
    --page: #121212;
    --card: #1c1c1d;
    --ink: #f2f2f2;
    --blue: #1a73c4;
    --ghost: #262627;
  }
  * { box-sizing: border-box; margin: 0; padding: 0; }
  html, body { width: 1200px; height: 1059px; overflow: hidden; background: var(--page); }
  .canvas { position: relative; width: 1200px; height: 1059px; }
  .card {
    position: absolute; left: 255px; width: 690px; height: 392px;
    background: var(--card); border-radius: 18px; overflow: hidden;
  }
  .card--realty { top: 90px; }
  .card--build { top: 547px; }

  .brand {
    position: absolute; left: 36px; display: flex; align-items: center; gap: 12px;
    font-family: "Cinzel", serif; font-weight: 600; color: var(--ink);
  }
  .card--realty .brand { top: 70px; font-size: 38px; }
  .card--build .brand { top: 62px; font-size: 40px; }
  .brand__mark { width: 14px; height: 14px; background: var(--blue); }

  .owner {
    position: absolute; right: 36px; top: 52px; text-align: right;
    font-family: "Cinzel", serif; font-size: 33px; color: var(--ink); letter-spacing: 0.5px;
  }
  .owner::after {
    content: ""; display: block; margin: 8px 0 0 auto; width: 48px; height: 2px; background: var(--blue);
  }

  .contacts {
    position: absolute; left: 36px; list-style: none;
    font-family: "Tinos", serif; color: var(--ink); font-size: 18.5px;
  }
  .card--realty .contacts { top: 210px; line-height: 24.8px; }
  .card--build .contacts { top: 250px; line-height: 29.5px; }
  .contacts li { display: flex; align-items: center; gap: 7px; }
  .contacts svg { width: 13px; height: 13px; flex: none; fill: var(--blue); }
  .dot { width: 10px; height: 10px; margin: 0 1.5px; border-radius: 50%; background: var(--blue); flex: none; }

  .partners {
    position: absolute; left: 253px; top: 325px; display: flex; align-items: center; gap: 16px;
    font-family: "Tinos", serif; font-size: 11px; color: var(--ink); text-transform: uppercase; letter-spacing: 0.5px;
  }

  .ghost {
    position: absolute; font-family: "Cinzel", serif; font-weight: 600; color: var(--ghost); line-height: 1;
  }
  .card--realty .ghost { right: 22px; bottom: 30px; font-size: 150px; }
  .card--build .ghost { right: 20px; bottom: 30px; font-size: 82px; text-align: right; line-height: 0.95; }
</style>
</head>
<body>
<main class="canvas">

  <section class="card card--realty" aria-label="Real estate side">
    <div class="brand"><span class="brand__mark"></span>TK Homes</div>
    <h1 class="owner">Marek Tove</h1>
    <ul class="contacts">
      <li><svg viewBox="0 0 16 16"><path d="M3 1l3 3-2 2c1 2 3 4 5 5l2-2 3 3-2 2C6 14 2 10 1 3z"/></svg>5558130467</li>
      <li><svg viewBox="0 0 16 16"><path d="M1 6l7-5 7 5v9H1zM2.5 7l5.5 4 5.5-4"/></svg>Marek@Marektove.example</li>
      <li><svg viewBox="0 0 16 16"><circle cx="8" cy="8" r="7"/></svg>www.Marektove.example</li>
      <li><svg viewBox="0 0 16 16"><path d="M8 0a5.5 5.5 0 0 0-5.5 5.5C2.5 10 8 16 8 16s5.5-6 5.5-10.5A5.5 5.5 0 0 0 8 0zm0 3.2a2.3 2.3 0 1 1 0 4.6 2.3 2.3 0 0 1 0-4.6z"/></svg>3847 61 St Nw</li>
      <li><span class="dot"></span>Marek_Bzq_Realtor</li>
      <li><span class="dot"></span>marekt</li>
    </ul>
    <div class="partners"><span>the Property quarter</span><span>Vox Realty</span></div>
    <div class="ghost" aria-hidden="true">TK</div>
  </section>

  <section class="card card--build" aria-label="Home building side">
    <div class="brand"><span class="brand__mark"></span>Stone Dorf</div>
    <h2 class="owner">Marek Tove</h2>
    <ul class="contacts">
      <li><svg viewBox="0 0 16 16"><path d="M3 1l3 3-2 2c1 2 3 4 5 5l2-2 3 3-2 2C6 14 2 10 1 3z"/></svg>5558130467</li>
      <li><svg viewBox="0 0 16 16"><path d="M1 6l7-5 7 5v9H1zM2.5 7l5.5 4 5.5-4"/></svg>Stonedorfdev@mailbox.example</li>
      <li><svg viewBox="0 0 16 16"><circle cx="8" cy="8" r="7"/></svg>www.stonedorfdev.example</li>
      <li><span class="dot"></span>Stonedorf_Bzq</li>
    </ul>
    <div class="ghost" aria-hidden="true">Stone<br>Dorf</div>
  </section>

</main>
</body>
</html>
```